New Website Design & Build Project - Lively Oak Dishes

I am looking for a professional clean looking website design then build of a website for my meal delivery business Lively Oak Dishes. I already have the domain - www.livelyoakdishes.com.au and I will upload brief for the design and layout of the website.

I have a dropbox full of photos, designs, videos and existing graphic design work that I can share with the designers. This can be provided upon designer request.

I am looking to build this site in WORDPRESS and I would like to build the site using the Velmora Page Composer - https://velmoraskins.example/

Target Market(s)

Kids from 2-16 , Teenagers - 16 - 19, Adults - 19 - 80 + - We Cater For Everyone

Industry/Entity Type

Health And Wellness

Coding

Coded - Design and coding required

Number of Pages Required

5+ page

Colors
33b8a4
abd037
ec1f27
fbee3f
3276b5

Requirements
Must have
• Must incorporate the included Lively Oak Dishes & LOD Logo
Must incorporate designs of packaging into website design.
Must keep text styles consistant throughout design
Must be mobile, tablet and desktop view responsive on all devices.
Must be built in Wordpress
The coder must have experience with velmora skins, velmora page composer, velmora prospects and also be very experienced with setting up products using Quillo Storefront plug in-
https://quillostorefront.example/
I want to integrate Postwren - https://dealbarn.example/postwren/ into site as well
Nice to have
• All of the above
Should not have
• No dark colours

```html
<!DOCTYPE html>
<html lang="en">
<head>
<meta charset="utf-8">
<title>Lively Oak Dishes</title>
<link href="https://fonts.googleapis.com/css2?family=Montserrat:wght@500;600;700;800&family=Roboto:wght@400;500&display=swap" rel="stylesheet">
<style>
:root{
  --green:#55b43a;
  --black:#0b0b0b;
  --ink:#151515;
  --cream:#f7f6f2;
  --footer-bg:#eef5e8;
  --footer-line:#cfdcc6;
  --yellow:#f6c414;
  --muted:#777;
  --white:#fff;
}
*{box-sizing:border-box;margin:0;padding:0}
html,body{width:715px;height:1200px;overflow:hidden;background:var(--white)}
body{position:relative;font-family:'Roboto',sans-serif;color:var(--ink)}
.abs{position:absolute}

/* top account bar */
.account-bar{left:438px;top:0;height:20px;width:173px;display:flex}
.account-bar a{font-family:'Montserrat',sans-serif;font-weight:700;font-size:8.5px;color:var(--white);text-decoration:none;display:flex;align-items:center;justify-content:center;height:20px}
.login{background:var(--green);width:62px;clip-path:polygon(0 0,100% 0,100% 100%,6% 100%)}
.signup{background:var(--black);width:113px;margin-left:-2px;clip-path:polygon(5% 0,100% 0,95% 100%,0 100%)}

/* header */
.brand{left:103px;top:40px;font-family:'Montserrat',sans-serif;font-weight:800;font-size:11.5px;color:var(--ink);line-height:16px;letter-spacing:.2px}
.main-nav{left:256px;top:43px;display:flex;gap:28px;font-family:'Montserrat',sans-serif;font-weight:600;font-size:8.6px;line-height:10px}
.main-nav span{color:var(--ink)}
.main-nav .active{color:var(--green)}
.nav-divider{left:551px;top:41px;width:1px;height:15px;background:#bbb}
.cart{left:565px;top:41px;display:flex;align-items:center;gap:3px;font-family:'Montserrat',sans-serif;font-weight:700;font-size:6.3px}
.cart-badge{left:574px;top:37px;width:8px;height:8px;border-radius:50%;background:var(--green);color:#fff;font-size:5px;display:flex;align-items:center;justify-content:center;font-family:'Montserrat',sans-serif;font-weight:700}

/* hero */
.hero{left:0;top:65px;width:715px;height:348px}
.hero-title{left:0;top:188px;width:715px;text-align:center;font-family:'Montserrat',sans-serif;font-weight:800;color:var(--yellow);text-shadow:0 2px 6px rgba(0,0,0,.45)}
.hero-title .l1{display:block;font-size:35px;line-height:40px;letter-spacing:.5px}
.hero-title .l2{display:block;font-size:28px;line-height:36px;margin-top:-2px}

/* subscription */
.subscribe-band{left:0;top:393px;width:715px;height:277px}
.subscribe-title{left:103px;top:452px;font-family:'Montserrat',sans-serif;font-weight:800;font-size:16px;line-height:19.5px;color:var(--ink)}
.accent-bar{height:5px;width:62px;background:var(--green);border-radius:3px}
.email-field{left:103px;top:518px;width:208px;height:28px;border-radius:14px;background:var(--white);border:1px solid #e5e5e5;display:flex;align-items:center;justify-content:center;font-family:'Montserrat',sans-serif;font-size:8.4px;color:var(--muted)}
.join-btn{left:103px;top:554px;width:208px;height:28px;border-radius:14px;background:var(--green);color:var(--white);display:flex;align-items:center;justify-content:center;font-family:'Montserrat',sans-serif;font-weight:700;font-size:8.4px;letter-spacing:.3px}
.subscribe-note{left:103px;top:594px;width:205px;font-size:9px;line-height:14.5px;color:#222}

/* meal plans */
.section-title{left:0;top:702px;width:715px;text-align:center;font-family:'Montserrat',sans-serif;font-weight:800;font-size:16px;color:var(--ink)}
.plans{left:102px;top:755px;display:flex;gap:10px}
.plan{width:120px;height:191px;background:var(--white);border:1px solid #e2e2e2;display:flex;flex-direction:column;align-items:center}
.plan.featured{box-shadow:0 4px 12px rgba(0,0,0,.14);border-color:#f0f0f0}
.plan-photo{width:100%;height:98px}
.plan-price{margin-top:9px;font-family:'Montserrat',sans-serif;font-weight:700;font-size:15.5px;color:var(--green);line-height:18px}
.plan-name{margin-top:7px;font-family:'Montserrat',sans-serif;font-weight:600;font-size:7.4px;line-height:8.8px;text-align:center;color:#222;height:18px}
.plan-btn{margin-top:12px;width:59px;height:18px;border-radius:9px;border:1.3px solid var(--green);color:var(--green);font-family:'Montserrat',sans-serif;font-weight:700;font-size:6.3px;display:flex;align-items:center;justify-content:center}
.plan.featured .plan-btn{background:var(--green);color:var(--white)}

/* footer */
.footer-rule{left:0;top:985px;width:715px;height:4px;background:var(--green)}
.footer{left:0;top:989px;width:715px;height:211px;background:var(--footer-bg)}
.footer-brand{left:105px;top:1040px;font-family:'Montserrat',sans-serif;font-weight:800;font-size:23px;color:var(--ink);letter-spacing:1px}
.footer-col{top:1030px;color:var(--ink)}
.footer-col h3{font-family:'Montserrat',sans-serif;font-weight:800;font-size:9.4px;margin-bottom:8px;letter-spacing:.2px}
.footer-col p{font-size:8.4px;line-height:17px;display:flex;align-items:center;gap:6px;color:#2a2a2a}
.social{display:flex;gap:7px;margin-top:4px}
.social span{width:12px;height:12px;border-radius:50%;border:1.5px solid var(--ink)}
.footer-divider{left:103px;top:1110px;width:509px;height:1px;background:var(--footer-line)}
.legal{left:0;top:1127px;width:715px;text-align:center;font-size:7.6px;color:#666}
.legal a{color:var(--green);text-decoration:underline}
.copyright{left:0;top:1150px;width:715px;text-align:center;font-size:8.2px;line-height:17px;color:#2a2a2a}
</style>
</head>
<body>

<nav class="abs account-bar">
  <a class="login" href="#">LOGIN</a>
  <a class="signup" href="#">MEMBER SIGN UP</a>
</nav>

<div class="abs brand">LIVELY OAK DISHES</div>

<nav class="abs main-nav">
  <span class="active">HOME</span>
  <span>CONTACT US</span>
  <span>MENU</span>
  <span>OAK LIFE BLOG</span>
</nav>
<div class="abs nav-divider"></div>
<div class="abs cart">
  <svg width="13" height="13" viewBox="0 0 24 24" fill="none" stroke="#151515" stroke-width="2.4"><path d="M2 3h3l3 11h11l2-8H7"/><circle cx="9" cy="19" r="1.8"/><circle cx="18" cy="19" r="1.8"/></svg>
  <span>CART(0)</span>
</div>
<div class="abs cart-badge">0</div>

<svg class="abs hero" viewBox="0 0 715 348" role="img" aria-label="Hero photo: bowl of salad with grilled chicken, spinach, tomatoes and cucumber on a grey stone table with forks">
  <defs>
    <radialGradient id="heroBowl" cx="62%" cy="55%" r="55%">
      <stop offset="0" stop-color="#a0855a"/>
      <stop offset=".45" stop-color="#5e7140"/>
      <stop offset="1" stop-color="#5a5a58"/>
    </radialGradient>
  </defs>
  <polygon points="0,0 715,0 715,328 0,347" fill="url(#heroBowl)"/>
  <polyline points="40,153 30,163 40,173" fill="none" stroke="#fff" stroke-width="1.2"/>
  <polyline points="684,153 694,163 684,173" fill="none" stroke="#fff" stroke-width="1.2"/>
</svg>
<h1 class="abs hero-title"><span class="l1">WEIGHTLOSS</span><span class="l2">STRENGTH &amp; TONING</span></h1>

<svg class="abs subscribe-band" viewBox="0 0 715 277">
  <defs>
    <linearGradient id="mealShot" x1="0" y1="0" x2="1" y2="1">
      <stop offset="0" stop-color="#7a5a3a"/>
      <stop offset=".5" stop-color="#4d6b2a"/>
      <stop offset="1" stop-color="#3a2a1c"/>
    </linearGradient>
  </defs>
  <polygon points="0,19 715,0 715,277 0,277" fill="#f7f6f2"/>
  <polygon points="428,85 715,9 715,277 440,277 416,100" fill="url(#mealShot)" role="img" aria-label="Photo: sliced glazed chicken with broccoli and chilli"/>
</svg>

<h2 class="abs subscribe-title">LIVELY OAK DISHES<br>SUBSCRIPTION SERVICE</h2>
<div class="abs accent-bar" style="left:103px;top:497px"></div>
<div class="abs email-field">Email Address</div>
<div class="abs join-btn">JOIN NOW</div>
<p class="abs subscribe-note">Join the Lively Oak Dishes subscription service to get the lowest prices. Cancel anytime</p>

<h2 class="abs section-title">MEAL PLANS</h2>
<div class="abs accent-bar" style="left:327px;top:732px"></div>

<div class="abs plans">
  <article class="plan">
    <div class="plan-photo" role="img" aria-label="Photo: kids meal bowls with roasted vegetables" style="background:linear-gradient(135deg,#6b4a35,#a65a34 50%,#4a4a48)"></div>
    <div class="plan-price">$35</div>
    <div class="plan-name">LOD KIDS 7 DAY<br>MEAL PLAN</div>
    <div class="plan-btn">JOIN NOW</div>
  </article>
  <article class="plan featured">
    <div class="plan-photo" role="img" aria-label="Photo: bowl of fresh fruit and vegetables on a kitchen bench" style="background:linear-gradient(135deg,#3d3d3a,#b58a3a 45%,#4f7a32)"></div>
    <div class="plan-price">$54</div>
    <div class="plan-name">LOD ADULT 7 DAY<br>MEAL PLAN</div>
    <div class="plan-btn">JOIN NOW</div>
  </article>
  <article class="plan">
    <div class="plan-photo" role="img" aria-label="Photo: meal containers with wraps and broccoli" style="background:linear-gradient(135deg,#8a8a86,#3a3a30 45%,#6b7a3a)"></div>
    <div class="plan-price">$108</div>
    <div class="plan-name">LOD ADULT 7 DAY<br>COUPLES MEAL PLAN</div>
    <div class="plan-btn">JOIN NOW</div>
  </article>
  <article class="plan">
    <div class="plan-photo" role="img" aria-label="Photo: meal containers with rice and roasted vegetables beside a tray" style="background:linear-gradient(135deg,#9a9a96,#2d2d2a 45%,#a55a30)"></div>
    <div class="plan-price">$162</div>
    <div class="plan-name">LOD ADULT 21 MEALS<br>PER WEEK PLAN</div>
    <div class="plan-btn">JOIN NOW</div>
  </article>
</div>

<div class="abs footer-rule"></div>
<footer class="abs footer"></footer>
<div class="abs footer-brand">LOD</div>

<div class="abs footer-col" style="left:227px">
  <h3>CONTACT US</h3>
  <p><svg width="9" height="7" viewBox="0 0 18 13"><rect width="18" height="13" rx="1.5" fill="#55b43a"/><path d="M1 1l8 6 8-6" fill="none" stroke="#eef5e8" stroke-width="1.6"/></svg>hello@livelyoakkitchen.com</p>
  <p><svg width="9" height="9" viewBox="0 0 24 24"><path d="M6.6 10.8a15 15 0 006.6 6.6l2.2-2.2a1 1 0 011-.25 11 11 0 003.6.6 1 1 0 011 1V20a1 1 0 01-1 1A17 17 0 013 4a1 1 0 011-1h3.5a1 1 0 011 1c0 1.25.2 2.45.6 3.6a1 1 0 01-.25 1z" fill="#55b43a"/></svg>Phone:0400 118 273</p>
</div>
<div class="abs footer-col" style="left:400px">
  <h3>OPENING HOURS</h3>
  <p>Mon- Friday – 9 – 5 pm</p>
  <p>Sat – 8 am – 12 pm</p>
</div>
<div class="abs footer-col" style="left:534px">
  <h3>SOCIAL MEDIA</h3>
  <div class="social"><span aria-label="Social profile one"></span><span aria-label="Social profile two"></span></div>
</div>

<div class="abs footer-divider"></div>
<div class="abs legal"><a href="#">DISCLAIMER</a> &nbsp;| &nbsp;<a href="#">TERMS &amp; CONDITION</a> &nbsp;| &nbsp;<a href="#">PRIVACY – POLICY</a></div>
<div class="abs copyright">Copyright – 2020 – Lively Oak Dishes Pty Ltd – ABN – 12 345 678 901<br>Shop 4 – 27 Fernlea Lane, Marrowdale, QLD, 4999</div>

</body>
</html>
```